Business Card Design Project

Business card based on attached logo

Todd Merrick
Todd@lorvantest.com
877-514-9073 ext. 318
Www.LorvanTest.com

Industry/Entity Type

Business

```html
<!DOCTYPE html>
<html lang="en">
<head>
<meta charset="utf-8">
<title>LorvanTest Business Cards</title>
<link href="https://fonts.googleapis.com/css2?family=Archivo+Black&family=Jost:wght@400;500;600&display=swap" rel="stylesheet">
<style>
  :root {
    --brand-red: #e8262b;
    --brand-black: #231f20;
    --card-white: #ffffff;
    --backdrop: #e6e2de;
    --text-dark: #231f20;
    --divider: #c9c9c9;
  }
  * { box-sizing: border-box; margin: 0; padding: 0; }
  html, body {
    width: 1200px;
    height: 715px;
    overflow: hidden;
    background: var(--backdrop);
  }
  .sheet {
    position: relative;
    width: 1200px;
    height: 715px;
  }
  .card {
    position: absolute;
    width: 506px;
    height: 288px;
    border-radius: 16px;
    overflow: hidden;
    box-shadow: 0 3px 10px rgba(0,0,0,0.18);
  }
  .card--front { left: 54px; top: 47px; background: var(--card-white); }
  .card--white { left: 623px; top: 37px; background: var(--card-white); }
  .card--red   { left: 51px; top: 379px; background: var(--brand-red); }
  .card--black { left: 629px; top: 381px; background: var(--brand-black); }

  .wordmark {
    position: absolute;
    display: flex;
    align-items: center;
    gap: 10px;
    font-family: "Archivo Black", "Arial Black", sans-serif;
    font-weight: 400;
    letter-spacing: -0.5px;
    line-height: 1;
    white-space: nowrap;
  }
  .wordmark__square { display: block; flex: none; }

  .card--front .wordmark {
    left: 28px; top: 118px;
    font-size: 25px;
    color: var(--brand-black);
    gap: 7px;
  }
  .card--front .wordmark__square { width: 14px; height: 14px; background: var(--brand-red); }

  .card--large .wordmark {
    left: 0; right: 0; top: 104px;
    justify-content: center;
    font-size: 52px;
  }
  .card--large .wordmark__square { width: 22px; height: 22px; }
  .card--white .wordmark { color: var(--brand-black); }
  .card--white .wordmark__square { background: var(--brand-red); }
  .card--red .wordmark { color: var(--card-white); }
  .card--red .wordmark__square { background: var(--card-white); }
  .card--black .wordmark { color: var(--card-white); }
  .card--black .wordmark__square { background: var(--card-white); }

  .web-address {
    position: absolute;
    left: 0; right: 0; bottom: 18px;
    text-align: center;
    font-family: "Jost", sans-serif;
    font-weight: 500;
    font-size: 15px;
    letter-spacing: 2.6px;
  }
  .card--white .web-address { color: var(--text-dark); }
  .card--red .web-address,
  .card--black .web-address { color: var(--card-white); }

  .divider {
    position: absolute;
    left: 284px; top: 76px;
    width: 1px; height: 112px;
    background: var(--divider);
  }
  .contact {
    position: absolute;
    left: 296px; top: 78px;
    font-family: "Jost", sans-serif;
    color: var(--text-dark);
  }
  .contact__name {
    font-weight: 600;
    font-size: 19px;
    letter-spacing: 1.4px;
    color: var(--brand-red);
    margin-bottom: 14px;
  }
  .contact__line {
    display: flex;
    align-items: center;
    gap: 6px;
    font-size: 13.5px;
    height: 24.5px;
  }
  .contact__icon { width: 10px; height: 10px; flex: none; }
  .contact__icon path,
  .contact__icon circle,
  .contact__icon rect { fill: var(--brand-red); }
  .contact__icon .stroke { fill: none; stroke: var(--card-white); stroke-width: 1; }

  .footer-bands {
    position: absolute;
    left: 0; bottom: 0;
    width: 506px; height: 36px;
  }
  .footer-bands .band-black { fill: var(--brand-black); }
  .footer-bands .band-red { fill: var(--brand-red); }
</style>
</head>
<body>
<main class="sheet">

  <section class="card card--front" aria-label="Business card front">
    <div class="wordmark"><span class="wordmark__square"></span>LorvanTest</div>
    <div class="divider"></div>
    <div class="contact">
      <p class="contact__name">Todd Merrick</p>
      <p class="contact__line">
        <svg class="contact__icon" viewBox="0 0 10 10" aria-hidden="true">
          <circle cx="5" cy="5" r="5"/>
          <path class="stroke" d="M3.3 2.4 L4.2 3.6 L3.7 4.3 Q4.6 5.8 5.8 6.4 L6.5 5.9 L7.6 6.8 L7 7.7 Q4.2 7.2 2.6 3.1 Z"/>
        </svg>
        877-514-9073 ext. 318
      </p>
      <p class="contact__line">
        <svg class="contact__icon" viewBox="0 0 10 10" aria-hidden="true">
          <circle cx="5" cy="5" r="5"/>
          <rect class="stroke" x="2.5" y="3.2" width="5" height="3.6"/>
          <path class="stroke" d="M2.5 3.2 L5 5.2 L7.5 3.2"/>
        </svg>
        Todd@lorvantest.com
      </p>
      <p class="contact__line">
        <svg class="contact__icon" viewBox="0 0 10 10" aria-hidden="true">
          <circle cx="5" cy="5" r="5"/>
          <circle class="stroke" cx="5" cy="5" r="2.8"/>
          <path class="stroke" d="M2.2 5 H7.8 M5 2.2 Q3.4 5 5 7.8 M5 2.2 Q6.6 5 5 7.8"/>
        </svg>
        www.LorvanTest.com
      </p>
    </div>
    <svg class="footer-bands" viewBox="0 0 506 36" aria-hidden="true">
      <polygon class="band-black" points="0,19 284,19 276,36 0,36"/>
      <polygon class="band-red" points="301,19 506,19 506,36 293,36" transform="translate(0,0)"/>
      <polygon class="band-red" points="310,0 506,0 506,36 293,36"/>
    </svg>
  </section>

  <section class="card card--large card--white" aria-label="Business card back, white">
    <div class="wordmark">LorvanTest<span class="wordmark__square"></span></div>
    <p class="web-address">www.LorvanTest.com</p>
  </section>

  <section class="card card--large card--red" aria-label="Business card back, red">
    <div class="wordmark">LorvanTest<span class="wordmark__square"></span></div>
    <p class="web-address">www.LorvanTest.com</p>
  </section>

  <section class="card card--large card--black" aria-label="Business card back, black">
    <div class="wordmark">LorvanTest<span class="wordmark__square"></span></div>
    <p class="web-address">www.LorvanTest.com</p>
  </section>

</main>
</body>
</html>
```